Detail Shop Business card design

i need a business card design for my new detailing company called 'Brisk's Polish Works'. i want an all black and white design . simple, direct and to the point. i want the designer to choose a fitting font to match the logothe front should have logo, address, phone and email and the back side should have a slogan and text indicating that we offer services on anything including cars, trucks, motorcycles and RVs. slogan will read "we take pride in your ride"
maybe also very small on the back side the IG icon with Brisks_Polish_Works

phone 208.417.6352
address 3847 E Larkin Ave
Spokane WA 99214
email: BrisksPolish@mailvexo.com

Target Market(s)

all ages , auto enthusiasts

Industry/Entity Type

Automotive

Contact Information for Business Card

the front should have logo, address, phone and email and the back side should have a slogan and text indicating that we offer services on anything including cars, trucks, motorcycles and RVs. slogan will read "we take pride in your ride"

phone 208.417.6352
address 3847 E Larkin Ave
Spokane WA 99214

Colors
000000
ffffff

Requirements
Must have
• bold font and very simple design with good spacing
Nice to have
• anything creative from the designer indicating we service any types of vehicles
Should not have
• any colors ,

```html
<!DOCTYPE html>
<html lang="en">
<head>
<meta charset="utf-8">
<title>Brisk's Polish Works – Business Card</title>
<link rel="stylesheet" href="https://fonts.googleapis.com/css2?family=Oswald:wght@500;600&family=Roboto+Condensed:wght@300;400;700&display=swap">
<style>
  :root {
    --ink: #111111;
    --paper: #ffffff;
    --stage: #ececec;
    --rule: #3a3a3a;
    --muted: #555555;
    --back-card: #585858;
    --back-ink: #161616;
    --bevel: #9a9a9a;
  }
  * { box-sizing: border-box; margin: 0; padding: 0; }
  html, body { width: 1200px; height: 950px; overflow: hidden; }
  body {
    background: var(--stage);
    font-family: "Roboto Condensed", Arial, sans-serif;
    position: relative;
  }
  .card {
    position: absolute;
    width: 640px;
    height: 366px;
    overflow: hidden;
    box-shadow: 0 10px 28px rgba(0,0,0,0.25);
  }

  /* Front */
  .card-front { left: 70px; top: 90px; background: var(--paper); color: var(--ink); }
  .brand {
    position: absolute; right: 44px; top: 46px;
    display: flex; align-items: center; gap: 12px;
  }
  .brand-dot { width: 34px; height: 34px; border-radius: 50%; background: var(--ink); }
  .brand-name { font-weight: 700; font-size: 26px; letter-spacing: 0.5px; text-transform: uppercase; }
  .holder { position: absolute; left: 46px; top: 140px; }
  .holder-name { font-weight: 700; font-size: 30px; letter-spacing: 0.5px; line-height: 1; }
  .holder-role { font-weight: 300; font-size: 19px; color: var(--muted); margin-top: 4px; }
  .divider { position: absolute; left: 40px; right: 40px; top: 218px; height: 1.5px; background: var(--rule); }
  .contacts { position: absolute; left: 46px; top: 232px; list-style: none; }
  .contacts li { display: flex; align-items: center; gap: 10px; font-size: 16px; line-height: 25px; font-weight: 400; }
  .contacts svg { width: 14px; height: 14px; flex: none; }
  .address { position: absolute; right: 44px; top: 234px; text-align: right; font-size: 17px; line-height: 24px; color: #333; }
  .base-band { position: absolute; left: 0; bottom: 0; width: 640px; height: 48px; }
  .site {
    position: absolute; right: 36px; bottom: 12px;
    color: var(--paper); font-size: 17px; letter-spacing: 4px; font-weight: 400;
  }

  /* Back */
  .card-back { left: 490px; top: 478px; background: var(--back-card); color: var(--back-ink); }
  .vehicle-art {
    position: absolute; left: 150px; top: 34px; width: 420px; height: 200px;
    border-radius: 40px 90px 30px 30px;
    background: linear-gradient(100deg, #2a2a2a, #0e0e0e 60%, #333333);
  }
  .slogan-block { position: absolute; left: 40px; top: 252px; width: 560px; }
  .slogan { font-family: "Oswald", Arial, sans-serif; font-weight: 600; font-size: 27px; letter-spacing: 1px; text-transform: uppercase; }
  .slogan-rule { height: 2px; background: var(--back-ink); margin: 6px 0 8px; width: 440px; }
  .services { font-size: 16px; font-weight: 700; }
</style>
</head>
<body>

<section class="card card-front" aria-label="Business card front">
  <div class="brand">
    <span class="brand-dot"></span>
    <span class="brand-name">Brisk's Polish Works</span>
  </div>

  <div class="holder">
    <h1 class="holder-name">DANA REYES</h1>
    <p class="holder-role">CEO/FOUNDER</p>
  </div>

  <div class="divider"></div>

  <ul class="contacts">
    <li>
      <svg viewBox="0 0 16 16"><path d="M3 1.5l3 3-1.6 1.8c.9 2 2.4 3.5 4.3 4.4L10.5 9l3 3-1.8 2.4C6.5 14.2 1.8 9.5 1.5 3.3z" fill="currentColor"/></svg>
      208.417.6352
    </li>
    <li>
      <svg viewBox="0 0 16 16"><rect x="4" y="1" width="8" height="14" rx="1.5" fill="none" stroke="currentColor" stroke-width="1.5"/><circle cx="8" cy="12.5" r="0.9" fill="currentColor"/></svg>
      836 271 5048
    </li>
    <li>
      <svg viewBox="0 0 16 16"><rect x="1" y="3" width="14" height="10" fill="currentColor"/><path d="M1.5 3.5L8 9l6.5-5.5" fill="none" stroke="#fff" stroke-width="1.2"/></svg>
      BrisksPolish@mailvexo.com
    </li>
  </ul>

  <address class="address" style="font-style:normal">
    3847 E Larkin Ave<br>
    Spokane WA 99214
  </address>

  <svg class="base-band" viewBox="0 0 640 48" aria-hidden="true">
    <polygon points="0,26 316,26 338,0 640,0 640,48 0,48" fill="var(--bevel)"/>
    <polygon points="322,26 344,0 640,0 640,48 322,48" fill="var(--ink)"/>
  </svg>
  <p class="site">www.briskspolish.com</p>
</section>

<section class="card card-back" aria-label="Business card back">
  <div class="vehicle-art" role="img" aria-label="Black silhouette illustration of a classic hot rod car"></div>
  <div class="slogan-block">
    <h2 class="slogan">We take pride in your ride</h2>
    <div class="slogan-rule"></div>
    <p class="services">Services on anything including cars, trucks, motorcycles &amp; RVs</p>
  </div>
</section>

</body>
</html>
```